Banner für Immobilienmakler
Zielgruppe
Immobilienmakler, Immobilienverkauf mit Herz,
Aufgabenstellung
Verkauf von Häusern und Wohnungen, der Banner soll an einen Balkon oder einen Zaun angebracht werden mit dem Hinweis, dass das Haus Zu verkaufen ist.
Maße ca. 76 x 244cm
Es darf gerne frech und modern sein mit einem witzigen einladenden Spruch sein, sollte aber auch ansonsten zu meinem chicen Style passen (siehe Homepage www.karwendimmobilien.de) es soll sich abheben von anderen langweiligen Bannern.
Ggf soll die Plane auch noch an einem Tennisplatz angebracht werden

```html
<!DOCTYPE html>
<html lang="en">
<head>
<meta charset="utf-8">
<title>House for Sale Banner – Karwend Immobilien</title>
<link href="https://fonts.googleapis.com/css2?family=Poppins:wght@400;600;700&display=swap" rel="stylesheet">
<style>
  :root {
    --page-bg: #d6d6d6;
    --banner-dark: #151515;
    --gold: #bf9f67;
    --white: #ffffff;
  }
  * { margin: 0; padding: 0; box-sizing: border-box; }
  html, body { width: 1200px; height: 1200px; overflow: hidden; background: var(--page-bg); }
  body { position: relative; font-family: "Poppins", sans-serif; }

  .banner {
    position: absolute; left: 35px; top: 420px;
    width: 1133px; height: 361px;
    background: var(--banner-dark);
    overflow: hidden;
  }
  .banner-shapes { position: absolute; inset: 0; }

  .headline {
    position: absolute; left: 592px; top: 40px; width: 343px;
    font-weight: 700; font-size: 103px; line-height: 1;
    color: var(--gold); letter-spacing: 1px; text-align: center;
  }
  .subline {
    position: absolute; left: 652px; top: 152px; width: 222px;
    font-weight: 400; font-size: 44px; line-height: 1;
    color: var(--white); text-align: center; letter-spacing: 1px;
  }
  .rule { position: absolute; top: 173px; height: 3px; background: var(--gold); }
  .rule-left { left: 477px; width: 166px; }
  .rule-right { left: 882px; width: 251px; }

  .brand {
    position: absolute; left: 1013px; top: 30px; width: 110px;
    display: flex; flex-direction: column; align-items: center; gap: 8px;
    color: var(--white); font-weight: 600; font-size: 14px; line-height: 1.25;
    letter-spacing: .5px; text-align: center;
  }
  .brand-dot { width: 26px; height: 26px; border-radius: 50%; background: var(--white); }

  .phone-icon { position: absolute; left: 438px; top: 275px; width: 47px; height: 58px; }
  .contact-phone { position: absolute; left: 494px; top: 272px; }
  .contact-label { font-size: 14px; color: var(--white); line-height: 1.2; }
  .contact-number { font-size: 21px; color: var(--gold); line-height: 1.2; letter-spacing: .3px; }

  .mail-icon { position: absolute; left: 964px; top: 284px; width: 39px; height: 24px; }
  .contact-email {
    position: absolute; right: 20px; top: 312px;
    font-size: 22px; color: var(--white); letter-spacing: .3px; line-height: 1;
  }
</style>
</head>
<body>
  <div class="banner">
    <svg class="banner-shapes" viewBox="0 0 1133 361" width="1133" height="361">
      <defs>
        <linearGradient id="interior" x1="0" y1="0" x2="1" y2="1">
          <stop offset="0" stop-color="#2a2a2a"/>
          <stop offset="1" stop-color="#0f0f0f"/>
        </linearGradient>
        <linearGradient id="exterior" x1="0" y1="0" x2="0" y2="1">
          <stop offset="0" stop-color="#6fa6dc"/>
          <stop offset="0.45" stop-color="#d9dde2"/>
          <stop offset="1" stop-color="#4a4a4a"/>
        </linearGradient>
      </defs>
      <rect width="1133" height="361" fill="url(#interior)" role="img" aria-label="Dimmed photo of a furnished room inside the house"/>
      <path d="M0 0 H458 C500 70 470 210 288 361 H0 Z" fill="url(#exterior)" role="img" aria-label="Photo of the white terraced house with red accent wall under blue sky"/>
      <path d="M458 0 H505 C565 120 480 280 312 361 H288 C445 255 505 95 458 0 Z" fill="var(--gold)"/>
    </svg>

    <div class="brand"><span class="brand-dot"></span><span>Karwend<br>Immobilien</span></div>

    <h1 class="headline">HOUSE</h1>
    <span class="rule rule-left"></span>
    <p class="subline">FOR SALE</p>
    <span class="rule rule-right"></span>

    <svg class="phone-icon" viewBox="0 0 47 58" aria-hidden="true">
      <rect x="0" y="0" width="47" height="52" rx="4" fill="var(--gold)"/>
      <rect x="0" y="54" width="47" height="3" fill="var(--gold)"/>
      <path d="M10 14 c2-3 5-3 6 0 l2 4 c1 2 0 3-2 4 c2 5 5 8 9 10 c1-2 2-3 4-2 l4 2 c3 1 3 4 0 6 c-3 2-7 2-11-1 c-6-4-10-9-13-15 c-1-3-1-6 1-8 z" fill="var(--white)"/>
    </svg>
    <div class="contact-phone">
      <p class="contact-label">More information call us</p>
      <p class="contact-number">0171 – 482 36 90</p>
      <p class="contact-number">02241 – 55 60 712</p>
    </div>

    <svg class="mail-icon" viewBox="0 0 39 24" aria-hidden="true">
      <rect width="39" height="24" fill="var(--gold)"/>
      <path d="M0 0 L19.5 14 L39 0 M0 24 L15 11 M39 24 L24 11" stroke="var(--banner-dark)" stroke-width="1.5" fill="none"/>
    </svg>
    <p class="contact-email">info@karwendimmobilien.de</p>
  </div>
</body>
</html>
```